Home Security check flyer

I am a locksmith company. Wanting a flyer designed for postal delivery to houses.
The design is to have a home security check list similar to the one attached (Not exactly the same) targeting locks with some pictures of deadlocks, Deadbolts, Window Locks, Security door locks Etc..
The idea is to get people in there homes to make sure they are secure and if not to call us for a free quote.
Flyer is to catch customers eye so they don't just throw it our. E.G. IS YOUR HOME SECURE on the front
A4 Size to be folded to twice to envelope size.
My company information can be found at
www.tarvencroftkeys.com.au

Reason: Want to try a few changes on some of the eliminated ones.

Target Market(s)

residential homes (Security)

Industry/Entity Type

Locksmith

Requirements
Must have
• My logo and contact information
Based on information from www.tarvencroftkeys.com.au

```html
<!DOCTYPE html>
<html lang="en">
<head>
<meta charset="utf-8">
<title>Home Security Audit – Tarvencroft Keys</title>
<link rel="stylesheet" href="https://fonts.googleapis.com/css2?family=Arimo:wght@400;700&family=Open+Sans:wght@400;600&display=swap">
<style>
:root{
  --red:#c1272d;
  --red-soft:#e8a3a7;
  --ink:#222;
  --white:#fff;
  --backdrop:#e9e6e3;
  --silver-a:#f1f1f1;
  --silver-b:#9b9b9b;
}
*{box-sizing:border-box;margin:0;padding:0}
html,body{width:1200px;height:960px;overflow:hidden;background:var(--backdrop)}
body{position:relative;font-family:"Arimo",Arial,sans-serif;color:var(--ink)}
.page{position:absolute;background:var(--white);box-shadow:0 3px 12px rgba(0,0,0,.25);overflow:hidden}
.page--audit{left:41px;top:94px;width:545px;height:771px}
.page--extra{left:613px;top:100px;width:544px;height:770px}
.header{position:absolute;left:0;top:0;width:100%;height:161px;background:var(--red);color:var(--white)}
.page--extra .header{height:162px}
.title{position:absolute;left:25px;top:14px;font:700 34px/1 "Arimo",Arial,sans-serif;color:var(--white)}
.intro{position:absolute;left:25px;top:64px;width:360px;font:400 9.8px/13px "Open Sans",Arial,sans-serif}
.intro-q{position:absolute;left:25px;top:144px;font:400 9.8px/1 "Open Sans",Arial,sans-serif}
.photo{position:absolute;border-radius:4px}
.photo--hands{left:398px;top:0;width:121px;height:161px;border-radius:0;background:linear-gradient(160deg,#3b3b3b,#111 60%,#d9d9d9)}
.product{background:radial-gradient(circle at 35% 35%,var(--silver-a),var(--silver-b))}
.product--dark{background:radial-gradient(circle at 40% 35%,#666,#111)}
.status{position:absolute;top:176px;font:600 11px/1 "Open Sans",Arial,sans-serif;color:var(--red)}
.status--left{left:25px;text-transform:uppercase}
.status--right{right:12px;font-family:"Arimo",Arial,sans-serif;font-weight:700;font-size:11.4px}
.group{position:absolute;left:17px;width:516px;border:1px solid var(--red-soft)}
.group-title{position:absolute;left:25px;font:400 14px/14px "Arimo",Arial,sans-serif;color:var(--red)}
.row{position:absolute;left:25px;width:430px;height:14px;display:grid;grid-template-columns:122px 8px 14px 18px 8px 14px 8px 1fr;align-items:center;font-size:9.3px}
.row .label{grid-column:1}
.row .yes{grid-column:2}
.row .box-y{grid-column:3}
.row .no{grid-column:5}
.row .box-n{grid-column:6}
.row .note{grid-column:8;font-size:6.9px;line-height:8px;white-space:nowrap}
.box{display:block;width:14px;height:14px;border:1px solid var(--red-soft);background:var(--white)}
.row--extra{left:35px;width:490px;grid-template-columns:120px 8px 14px 17px 8px 14px 17px 1fr}
.row--extra .note{white-space:normal;font-size:7.2px;line-height:8.4px}
.section-title{position:absolute;left:36px;font:700 9.4px/1 "Arimo",Arial,sans-serif}
.personal-title{position:absolute;left:38px;top:436px;font:700 12.4px/1 "Arimo",Arial,sans-serif}
.question{position:absolute;left:38px;width:412px}
.question h3{font:400 12px/14px "Arimo",Arial,sans-serif}
.question p{font-size:7.3px;line-height:10.8px}
.answer{position:absolute;left:465px;width:55px;height:14px;display:grid;grid-template-columns:9px 14px 16px 9px 14px;align-items:center;font-size:8px}
.disclaimer{position:absolute;left:32px;top:666px;width:300px;font-size:7.3px;line-height:14.2px}
.seal{position:absolute;left:462px;top:664px;width:46px;height:46px;border-radius:50%;background:var(--red);border:3px solid #1f3c8a}
.footer{position:absolute;left:0;bottom:0;width:100%;height:50px;background:var(--red);color:var(--white);font-family:"Open Sans",Arial,sans-serif}
.footer-tag{position:absolute;left:15px;top:15px;font-size:12.2px}
.footer-url{position:absolute;right:16px;top:11px;font-size:16.4px}
.page--extra .footer-tag{left:31px;top:19px}
.page--extra .footer-url{top:17px}
</style>
</head>
<body>

<section class="page page--audit">
  <header class="header">
    <h1 class="title">Home Security Audit</h1>
    <p class="intro">House-breaking is one if the most comon crimes and can occur at any time day or night. This checklist is designed to help you take a fresh look at your security.<br>You can take steps to reduce identified risk areas in your home and reduce the likelihood of becoming a victim of crime or a repeat victim of crime.</p>
    <p class="intro-q">How does your home security rate?</p>
    <div class="photo photo--hands" role="img" aria-label="Photo of hands holding a small model house"></div>
  </header>

  <p class="status status--left">Present condition</p>
  <p class="status status--right">Consider making changes to the items ticked NO</p>

  <div class="group" style="top:190px;height:75px"></div>
  <div class="group" style="top:270px;height:111px"></div>
  <div class="group" style="top:386px;height:37px"></div>
  <div class="group" style="top:427px;height:91px"></div>
  <div class="group" style="top:523px;height:92px"></div>
  <div class="group" style="top:620px;height:93px"></div>

  <div class="photo product" style="left:458px;top:200px;width:64px;height:56px" role="img" aria-label="Security door knob lock"></div>
  <div class="photo product" style="left:467px;top:285px;width:41px;height:80px" role="img" aria-label="Digital keypad lock"></div>
  <div class="photo product" style="left:458px;top:390px;width:64px;height:29px" role="img" aria-label="Patio bolt lock"></div>
  <div class="photo product" style="left:470px;top:445px;width:52px;height:56px" role="img" aria-label="Deadbolt with key"></div>
  <div class="photo product" style="left:453px;top:540px;width:73px;height:56px" role="img" aria-label="Rim deadlock"></div>
  <div class="photo product product--dark" style="left:468px;top:637px;width:48px;height:57px" role="img" aria-label="Gate lock"></div>

  <h2 class="group-title" style="top:194px">Security Doors</h2>
  <div class="row" style="top:212px"><span class="label">At all entry/exits?</span><span class="yes">Y</span><span class="box box-y"></span><span class="no">N</span><span class="box box-n"></span><span class="note">Security doors deter intruders from entering your home</span></div>
  <div class="row" style="top:230px"><span class="label">Finger guards?</span><span class="yes">Y</span><span class="box box-y"></span><span class="no">N</span><span class="box box-n"></span><span class="note">Finger guards prevent the lock on your security door/s being tampered with</span></div>
  <div class="row" style="top:249px"><span class="label">Triple locks?</span><span class="yes">Y</span><span class="box box-y"></span><span class="no">N</span><span class="box box-n"></span><span class="note">Triple locks increase the strength and security of your doors</span></div>

  <h2 class="group-title" style="top:274px">Main Entry/Exit Doors</h2>
  <div class="row" style="top:292px"><span class="label">Front - solid core?</span><span class="yes">Y</span><span class="box box-y"></span><span class="no">N</span><span class="box box-n"></span><span class="note">Solid doors are preferred; the door should be as strong as the lock</span></div>
  <div class="row" style="top:310px"><span class="label">Front - viewer?</span><span class="yes">Y</span><span class="box box-y"></span><span class="no">N</span><span class="box box-n"></span><span class="note">Door viewers help you see who is outside your front door before you o</span></div>
  <div class="row" style="top:328px"><span class="label">Back - solid core?</span><span class="yes">Y</span><span class="box box-y"></span><span class="no">N</span><span class="box box-n"></span><span class="note">solid doors are preferred; hollow core doors should be avoided</span></div>
  <div class="row" style="top:346px"><span class="label">Adequate locks?</span><span class="yes">Y</span><span class="box box-y"></span><span class="no">N</span><span class="box box-n"></span><span class="note">Dead locks are the best type of lock to use on entry/exit doors</span></div>
  <div class="row" style="top:364px"><span class="label">Keyed alike?</span><span class="yes">Y</span><span class="box box-y"></span><span class="no">N</span><span class="box box-n"></span><span class="note">for safety and ease of use, one key opens all doors</span></div>

  <h2 class="group-title" style="top:389px">Sliding doors</h2>
  <div class="row" style="top:405px"><span class="label">Patio bolts?</span><span class="yes">Y</span><span class="box box-y"></span><span class="no">N</span><span class="box box-n"></span><span class="note">Keyed patio bolts on sliding doors strengthen the security of these doors</span></div>

  <h2 class="group-title" style="top:431px">Windows</h2>
  <div class="row" style="top:448px"><span class="label">Key operated locks?</span><span class="yes">Y</span><span class="box box-y"></span><span class="no">N</span><span class="box box-n"></span><span class="note">Key operated locks strengthen the security of your windows</span></div>
  <div class="row" style="top:466px"><span class="label">Keyed alike?</span><span class="yes">Y</span><span class="box box-y"></span><span class="no">N</span><span class="box box-n"></span><span class="note">For safety and ease of use, one key opens all windows</span></div>
  <div class="row" style="top:484px"><span class="label">Security screens?</span><span class="yes">Y</span><span class="box box-y"></span><span class="no">N</span><span class="box box-n"></span><span class="note">Security screens, grilles and shutters allow ventilation and can provide security</span></div>
  <div class="row" style="top:502px"><span class="label">Warning Stickers?</span><span class="yes">Y</span><span class="box box-y"></span><span class="no">N</span><span class="box box-n"></span><span class="note">Warning stickers may deter intruders from stealing your property</span></div>

  <h2 class="group-title" style="top:527px">Lighting</h2>
  <div class="row" style="top:544px"><span class="label">Main entry/exits?</span><span class="yes">Y</span><span class="box box-y"></span><span class="no">N</span><span class="box box-n"></span><span class="note">The main entry/exit areas to your home should be well lit</span></div>
  <div class="row" style="top:562px"><span class="label">Timers fitted?</span><span class="yes">Y</span><span class="box box-y"></span><span class="no">N</span><span class="box box-n"></span><span class="note">Lights left on inside your home when you are out often deter intruder</span></div>
  <div class="row" style="top:580px"><span class="label">Timers used?</span><span class="yes">Y</span><span class="box box-y"></span><span class="no">N</span><span class="box box-n"></span><span class="note">Timers should be activated when away from your home at night</span></div>
  <div class="row" style="top:598px"><span class="label">Sensor lighting?</span><span class="yes">Y</span><span class="box box-y"></span><span class="no">N</span><span class="box box-n"></span><span class="note">Sensor lighting in ' high risk' areas deter intruders from entering your home</span></div>

  <h2 class="group-title" style="top:624px">Property Marking</h2>
  <div class="row" style="top:641px"><span class="label">Engraved with code?</span><span class="yes">Y</span><span class="box box-y"></span><span class="no">N</span><span class="box box-n"></span><span class="note">Property engraving and using WARNING stickers on your property reduces<br>the risk of it being stolen</span></div>
  <div class="row" style="top:660px"><span class="label">Code recorded?</span><span class="yes">Y</span><span class="box box-y"></span><span class="no">N</span><span class="box box-n"></span><span class="note">Your property ID code should be recorded with police to assist them to contact<br>owners of recovered items</span></div>
  <div class="row" style="top:679px;height:24px"><span class="label">Inventory list?</span><span class="yes">Y</span><span class="box box-y"></span><span class="no">N</span><span class="box box-n"></span><span class="note">Recording serial numbers, makes, models and descriptions of your property<br>helps police recover stolen items and will assist you to make an insurance<br>claim (you may wish to photograph items and store somewhere safe)</span></div>

  <footer class="footer">
    <span class="footer-tag">Community Safety and Crime Prevention</span>
    <span class="footer-url">www.tarvencroftkeys.com.au</span>
  </footer>
</section>

<section class="page page--extra">
  <header class="header">
    <div class="photo product" style="left:15px;top:36px;width:94px;height:104px" role="img" aria-label="Door knob lock"></div>
    <div class="photo product" style="left:137px;top:31px;width:52px;height:113px" role="img" aria-label="Digital keypad lock"></div>
    <div class="photo product product--dark" style="left:208px;top:17px;width:80px;height:70px" role="img" aria-label="Gate lock"></div>
    <div class="photo product" style="left:287px;top:68px;width:99px;height:61px" role="img" aria-label="Deadbolt"></div>
    <div class="photo product" style="left:403px;top:17px;width:104px;height:51px" role="img" aria-label="Rim deadlock"></div>
    <div class="photo product" style="left:417px;top:83px;width:90px;height:52px" role="img" aria-label="Window lock"></div>
  </header>

  <h2 class="section-title" style="top:172px">Other safety considerations</h2>
  <div class="row row--extra" style="top:188px"><span class="label">Clear vision?</span><span class="yes">Y</span><span class="box box-y"></span><span class="no">N</span><span class="box box-n"></span><span class="note">Make sure all doors and windows can be seen clearly from outside</span></div>
  <div class="row row--extra" style="top:207px"><span class="label">Trees/shrubs trimmed?</span><span class="yes">Y</span><span class="box box-y"></span><span class="no">N</span><span class="box box-n"></span><span class="note">Trim any trees/shrubs that conceal doors and windows from being observed from the street</span></div>
  <div class="row row--extra" style="top:225px"><span class="label">Garage/shed secure?</span><span class="yes">Y</span><span class="box box-y"></span><span class="no">N</span><span class="box box-n"></span><span class="note">Garages and sheds should be securely locked at all time</span></div>
  <div class="row row--extra" style="top:243px"><span class="label">Tools secure?</span><span class="yes">Y</span><span class="box box-y"></span><span class="no">N</span><span class="box box-n"></span><span class="note">Lock tools away to prevent an intruder using them to get into your house</span></div>
  <div class="row row--extra" style="top:261px"><span class="label">Whwwlie bins secured?</span><span class="yes">Y</span><span class="box box-y"></span><span class="no">N</span><span class="box box-n"></span><span class="note">Lock whwwlie bins away or chain them to a fixed structure away from the house to prevent an intruder using them to climb into your home</span></div>
  <div class="row row--extra" style="top:279px"><span class="label">Gates to yard secured?</span><span class="yes">Y</span><span class="box box-y"></span><span class="no">N</span><span class="box box-n"></span><span class="note">Lock gates to the backyard with a keyed padlock to prevent access by intruders</span></div>
  <div class="row row--extra" style="top:298px"><span class="label">Meter box secured?</span><span class="yes">Y</span><span class="box box-y"></span><span class="no">N</span><span class="box box-n"></span><span class="note">Your electricity meter box should be locked (Contact your electricity provider to arrange)</span></div>
  <div class="row row--extra" style="top:315px"><span class="label">House numbers?</span><span class="yes">Y</span><span class="box box-y"></span><span class="no">N</span><span class="box box-n"></span><span class="note">House numbers should be clearly visible from the road</span></div>
  <div class="row row--extra" style="top:333px"><span class="label">Smoke alarms?</span><span class="yes">Y</span><span class="box box-y"></span><span class="no">N</span><span class="box box-n"></span><span class="note">Install smoke alarms and develop a frie evacuation plan</span></div>
  <div class="row row--extra" style="top:352px"><span class="label">Security alarms?</span><span class="yes">Y</span><span class="box box-y"></span><span class="no">N</span><span class="box box-n"></span><span class="note">Electronic security alarm systems deter intruders from entering your home</span></div>
  <div class="row row--extra" style="top:384px;align-items:start"><span class="label" style="margin-top:-14px;line-height:11px">Safe disposal of<br>personal documents?</span><span class="yes">Y</span><span class="box box-y"></span><span class="no">N</span><span class="box box-n"></span><span class="note" style="margin-top:-6px">All documents/ paperwork containing your personal details (e.g. old phone bills, medical invoices, power bills rates notices) should be totally destroyed before being placed in your wheelie bin for rubbish collection. Thiswill help protect you from identity theft. For more information on this refer to the HPS Identify Theft fact sheet.</span></div>

  <h2 class="personal-title">Personal Security in the Home</h2>
  <div class="question" style="top:456px"><h3>Do you keep information about your security arrangements private?</h3><p>Be aware of providing about your home security arrangements to people that do notneed to know this infomation. Highlighting your security weaknesses to others could be detrimental.</p></div>
  <div class="answer" style="top:460px"><span>Y</span><span class="box"></span><span></span><span>N</span><span class="box"></span></div>
  <div class="question" style="top:500px"><h3>Do you keep information about your personal arrangements private?</h3><p>Information about bank accounts and balances and personal particulars, including yourliving arrangements, should not be disclosed unnecessarily. Be conscious of also providing information to others about your planned absences from home.</p></div>
  <div class="answer" style="top:504px"><span>Y</span><span class="box"></span><span></span><span>N</span><span class="box"></span></div>
  <div class="question" style="top:555px"><h3>Do you store valuables out of sight and reach from outside?</h3><p>Oppertunistic thefts can occur when valuables are in clear view and within easy reach reach. valuables are best stored out of sight and in a secure location.</p></div>
  <div class="answer" style="top:558px"><span>Y</span><span class="box"></span><span></span><span>N</span><span class="box"></span></div>
  <div class="question" style="top:599px"><h3>Do you have important phone numbers stored in your phone?</h3><p>Having your local polica station number stored in your phone makes it easier to dial, especially in the dark. 000 (triple zero) can also be stored for use in emergencies. It is also useful to store the phone numbers of family and close friends for use by emergency services in the event of an incident.</p></div>
  <div class="answer" style="top:602px"><span>Y</span><span class="box"></span><span></span><span>N</span><span class="box"></span></div>

  <p class="disclaimer">DISCLAIMAR: This fact sheet contains general guidelines only. The Harbourline Police Service in providing this information makes no representations nor gives any warranty or guarantee concerning the safety of persons or property.</p>
  <div class="seal" role="img" aria-label="Trade association badge"></div>

  <footer class="footer">
    <span class="footer-tag">Community Safety and Crime Prevention</span>
    <span class="footer-url">www.tarvencroftkeys.com.au</span>
  </footer>
</section>

</body>
</html>
```